BrivoNest Learning App for Children with Dyslexia

Project Description:

We are seeking a talented UI/UX designer to create engaging and intuitive designs for Brivonest, an innovative educational app designed to help children learn letters and words through a multisensory learning approach. The app aims to be particularly helpful for children with dyslexia, providing a supportive and interactive learning environment.

Key App Features & Design Requirements:

Account Creation Screen: Design a welcoming and straightforward sign-up page that allows users to register with their email or continue with Quarnix. The design should be clean, focusing on user-friendliness and accessibility, adhering to our terms of service and privacy policy.

Main Screen Design: The main screen should allocate at least 4/6 of its height to the interactive drawing area. It needs to display word prompts in both correct and scrambled orders and include options to "Show all Words," "Play all words," and a search function. The interface should be vibrant, engaging, and easy to navigate for children.

Profile Section: Create a user-friendly profile page that allows users to edit their profile image, name, username, email, links, and bio. The design should be clean and encourage user engagement.

BrivoTally Page: This section will display the user's learning progress, including rankings, a learning curve, and recently learned words. It should visually represent progress in a motivating and understandable way, suitable for a younger audience.

Visual and Auditory Feedback Implementation: Incorporate elements that support visual and auditory feedback, using dyslexia-friendly formats. This includes choosing appropriate colors, fonts, and auditory cues.

Accessibility and Customization Settings: Designs should include settings for adjusting visual contrast, font size, and the word list to accommodate individual preferences and needs.

Feel free to add more interactions and/or pages.

Design preferences:

Color Scheme: Use a bright, inviting color palette that stimulates learning and engagement without overwhelming the users.
Font Selection: Opt for fonts that are readable and accessible, particularly for users with dyslexia.
Icons and Graphics: Design custom icons and graphics that are cohesive with the app's theme and purpose. Illustrations should be simple, relatable, and supportive of the learning process.

Target Market(s)

Educational

Industry/Entity Type

Educational

Colors
0054AA
0677BA
7BADD7
CADEEF
E8F1F8
0094D4
00A9DD
6FCCEA
C7EBF8
E9F6FB

Requirements
Must have
• Educational app, a writing area, scoring and account management
Nice to have
• Statistics, Ranking Page, Settings and some nice visual features

```html
<!DOCTYPE html>
<html lang="en">
<head>
<meta charset="utf-8">
<title>Brivonest – App Screens</title>
<link rel="stylesheet" href="https://fonts.googleapis.com/css2?family=Poppins:wght@400;500;600;700&family=Comic+Neue:wght@700&display=swap">
<style>
:root{
  --page:#efefef;
  --ink:#1f1f1f;
  --muted:#6b6b6b;
  --white:#ffffff;
  --field:#f1f1f1;
  --green:#6fcf00;
  --green-dark:#5cb800;
  --orange:#ff7a0f;
  --orange-light:#ff9a1a;
  --blue:#1f53b4;
  --blue-light:#2f7dd1;
  --cyan:#3fc7f0;
  --sky:#5fbdf4;
  --sky-light:#3aa9ef;
  --purple:#c05ff0;
  --purple-light:#d389f5;
  --lilac:#d57cf2;
  --violet:#9b59d0;
  --yellow:#ffb400;
  --chart:#c26bf2;
}
*{box-sizing:border-box;margin:0;padding:0}
html,body{width:1200px;height:618px;overflow:hidden;background:var(--page)}
body{position:relative;font-family:"Poppins",sans-serif;color:var(--ink)}
.screen-title{position:absolute;top:124px;width:220px;margin-left:-110px;text-align:center;font-size:13px;font-weight:400;color:#2a2a2a}
.screen{position:absolute;top:168px;width:150px;height:324px;border-radius:20px;overflow:hidden}
.abs{position:absolute}
.status{position:absolute;top:9px;left:10px;right:10px;display:flex;justify-content:space-between;font-size:7px;color:#fff}
.status-icons{display:flex;gap:2px;align-items:center}
.status-icons i{display:block;background:#fff;border-radius:1px}
.app-bar{position:absolute;top:26px;left:0;right:0;height:20px;display:flex;align-items:center;justify-content:center;font-family:"Comic Neue",sans-serif;font-weight:700;font-size:10px;color:#fff}
.menu{position:absolute;left:8px;top:7px;width:6px}
.menu i{display:block;height:1px;background:#fff;margin-bottom:1.3px}
.points{position:absolute;right:6px;top:7px;font-size:4.5px;font-weight:600;color:#fff;font-family:"Poppins",sans-serif}
.frame{position:absolute;left:4px;right:4px;top:52px;bottom:14px;border:1px solid rgba(255,255,255,.8);border-radius:3px}
.card{position:absolute;background:var(--white);border-radius:3px}
.ph{position:absolute;border-radius:6px}
.tiny{font-size:4.4px;color:var(--muted)}
/* login */
.login{left:103px;background:var(--green)}
.login .frame{top:24px}
.brand{position:absolute;top:38px;left:0;right:0;text-align:center;font-family:"Comic Neue",sans-serif;font-size:15px;font-weight:700;color:var(--ink)}
.center{position:absolute;left:0;right:0;text-align:center}
.field{position:absolute;left:4px;right:4px;height:18px;border-radius:2px;background:var(--field);font-size:5px;color:var(--muted);padding:6px 7px}
.btn{position:absolute;left:4px;right:4px;height:18px;border-radius:2px;display:flex;align-items:center;justify-content:center;font-size:5.5px;font-weight:500;color:#fff}
/* main */
.main-a{left:314px;background:linear-gradient(var(--orange) 0 14%,var(--orange-light))}
.main-b{left:514px;background:linear-gradient(var(--blue) 0 14%,var(--blue-light))}
.bar-line{position:absolute;top:46px;left:0;right:0;height:2px;background:rgba(255,255,255,.25)}
.drawing{left:9px;right:9px;top:60px;height:101px;display:flex;align-items:center;justify-content:center;font-size:7px;font-weight:500}
.panel{left:9px;right:9px;top:166px;height:132px}
.toggle{position:absolute;left:4px;right:4px;top:8px;height:22px;border:1px solid;border-radius:3px;display:flex;align-items:center;padding:2px}
.toggle span{flex:1;font-family:"Comic Neue",sans-serif;font-size:6.5px;color:#9a9a9a;padding-left:5px}
.toggle b{flex:1;height:100%;border-radius:3px;display:flex;align-items:center;justify-content:center;font-family:"Comic Neue",sans-serif;font-size:6.5px;color:#fff}
.word{position:absolute;width:38px;height:22px;border:1px solid;border-bottom-width:2px;border-radius:3px;display:flex;align-items:center;justify-content:center;font-size:4.5px;background:#fff}
.results{position:absolute;left:4px;right:4px;top:106px;height:19px;border-radius:3px;display:flex;align-items:center;justify-content:center;font-family:"Comic Neue",sans-serif;font-size:6px;color:#fff}
/* profile */
.profile{left:739px;background:linear-gradient(var(--sky) 0 14%,var(--sky-light))}
.avatar{position:absolute;border-radius:50%;background:radial-gradient(circle at 50% 40%,#c9a58c,#6b4a3a)}
.row{position:absolute;left:14px;right:6px;border-bottom:1px solid #eee;padding-bottom:3px}
.row .lab{font-size:3.8px;color:var(--muted)}
.row .val{font-size:5px;font-weight:600;color:var(--ink);line-height:1.6}
.row .chev{position:absolute;right:3px;top:4px;font-size:6px}
.row .ico{position:absolute;left:-9px;top:1px;width:4px;height:4px;border-radius:50%;background:#999}
/* stats */
.stats{left:957px;background:linear-gradient(var(--purple) 0 14%,var(--purple-light))}
.tab{position:absolute;top:60px;height:15px;border-radius:8px;font-size:5.5px;color:#fff;display:flex;align-items:center;justify-content:center}
.rank{position:absolute;top:83px;height:32px;border-radius:2px;color:#fff;padding:7px 5px}
.rank small{display:block;font-size:4.5px;font-weight:500}
.rank strong{display:block;font-size:9px;font-weight:600;white-space:nowrap}
.stat-card{left:8px;right:8px;padding:7px 5px}
.stat-card h3{font-size:6.5px;font-weight:500;margin-bottom:4px}
.list div{font-size:5px;border-bottom:1px solid #e7e7e7;padding:2.5px 0}
</style>
</head>
<body>

<div class="screen-title" style="left:220px">Login</div>
<div class="screen-title" style="left:386px">Main Screen sample 1</div>
<div class="screen-title" style="left:589px">Main Screen Sample 2</div>
<div class="screen-title" style="left:771px">Profile</div>
<div class="screen-title" style="left:1034px">BrivoTally</div>

<!-- Login -->
<section class="screen login">
  <div class="status"><span>9:41</span><span class="status-icons"><i style="width:5px;height:3px"></i><i style="width:4px;height:3px"></i><i style="width:7px;height:3px"></i></span></div>
  <div class="frame"></div>
  <div class="card" style="left:12px;right:12px;top:29px;bottom:20px">
    <div class="brand" style="top:10px">Brivonest</div>
    <div class="center tiny" style="top:31px;color:var(--ink)">Learn letters and words</div>
    <div class="ph" role="img" aria-label="Illustration of a bear reading a book on a grassy patch" style="left:0;right:0;top:45px;height:86px;border-radius:0 0 40% 40%/0 0 20% 20%;background:linear-gradient(#e8f2fb 0 55%,#c6e88a 80%,#b6dc6a)"></div>
    <div class="center" style="top:138px;font-family:'Comic Neue',sans-serif;font-weight:700;font-size:10px">Create An Account</div>
    <div class="center tiny" style="top:153px">Enter your email to sign up for this app</div>
    <div class="field" style="top:163px">Email Address</div>
    <div class="btn" style="top:185px;background:var(--green)">Sign up with email</div>
    <div class="center tiny" style="top:210px">or continue with</div>
    <div class="btn" style="top:220px;background:var(--field);color:var(--ink)"><span style="width:5px;height:5px;border-radius:50%;background:var(--green);margin-right:4px"></span>Login with Quarnix</div>
    <div class="center tiny" style="top:252px;line-height:1.4">By clicking continue, you agree to our<br><span style="color:var(--ink)">Terms of Service</span> and <span style="color:var(--ink)">Privacy Policy</span></div>
  </div>
</section>

<!-- Main screen sample 1 -->
<section class="screen main-a">
  <div class="status"><span>9:41</span><span class="status-icons"><i style="width:5px;height:3px"></i><i style="width:4px;height:3px"></i><i style="width:7px;height:3px"></i></span></div>
  <div class="app-bar"><span class="menu"><i></i><i></i><i></i></span>Main Screen<span class="points">16 Points</span></div>
  <div class="bar-line"></div>
  <div class="frame"></div>
  <div class="card drawing">Drawing Area</div>
  <div class="card panel">
    <div class="toggle" style="border-color:var(--violet)"><span>Show all Words</span><b style="background:var(--violet)">Play all words</b></div>
    <div class="word" style="left:4px;top:39px;border-color:var(--yellow)">Word 1</div>
    <div class="word" style="left:46px;top:39px;border-color:var(--yellow)">Word 2</div>
    <div class="word" style="left:88px;top:39px;border-color:var(--yellow)">Word 3</div>
    <div class="word" style="left:4px;top:66px;border-color:var(--yellow)">Word 4</div>
    <div class="word" style="left:46px;top:66px;border-color:var(--yellow)">…</div>
    <div class="ph" role="img" aria-label="Illustration of a giraffe with glasses" style="left:92px;top:64px;width:38px;height:68px;background:linear-gradient(#ffd27a,#f5a623)"></div>
    <div class="results" style="background:var(--orange)">Show me the results</div>
  </div>
</section>

<!-- Main screen sample 2 -->
<section class="screen main-b">
  <div class="status"><span>9:41</span><span class="status-icons"><i style="width:5px;height:3px"></i><i style="width:4px;height:3px"></i><i style="width:7px;height:3px"></i></span></div>
  <div class="app-bar"><span class="menu"><i></i><i></i><i></i></span>Main Screen<span class="points">16 Points</span></div>
  <div class="bar-line"></div>
  <div class="frame"></div>
  <div class="card drawing">Drawing Area</div>
  <div class="card panel">
    <div class="toggle" style="border-color:var(--green)"><span>Show all Words</span><b style="background:var(--green)">Play all words</b></div>
    <div class="word" style="left:4px;top:39px;border-color:var(--cyan)">Word 1</div>
    <div class="word" style="left:46px;top:39px;border-color:var(--cyan)">Word 2</div>
    <div class="word" style="left:88px;top:39px;border-color:var(--cyan)">Word 3</div>
    <div class="word" style="left:4px;top:66px;border-color:var(--cyan)">Word 4</div>
    <div class="word" style="left:46px;top:66px;border-color:var(--cyan)">…</div>
    <div class="ph" role="img" aria-label="Illustration of a giraffe with glasses" style="left:92px;top:64px;width:38px;height:68px;background:linear-gradient(#ffd27a,#f5a623)"></div>
    <div class="results" style="background:var(--lilac)">Show me the results</div>
  </div>
</section>

<!-- Profile -->
<section class="screen profile">
  <div class="status"><span>9:41</span><span class="status-icons"><i style="width:5px;height:3px"></i><i style="width:4px;height:3px"></i><i style="width:7px;height:3px"></i></span></div>
  <div class="app-bar"><span style="position:absolute;left:6px;font-family:Poppins,sans-serif;font-size:8px">‹</span>Profile</div>
  <div class="bar-line"></div>
  <div class="frame"></div>
  <div class="card" style="left:9px;right:9px;top:58px;bottom:20px">
    <div class="avatar" role="img" aria-label="Profile photo of the user" style="left:47px;top:5px;width:37px;height:37px"></div>
    <div class="abs" style="left:76px;top:31px;width:11px;height:11px;border-radius:50%;background:var(--yellow);border:1px solid #fff"></div>
    <div class="center" style="top:48px;font-size:7px;font-weight:500">Edit profile image</div>
    <div class="row" style="top:68px"><i class="ico"></i><div class="lab">Name</div><div class="val">Mara Ellison</div><span class="chev">›</span></div>
    <div class="row" style="top:89px"><i class="ico"></i><div class="lab">Username</div><div class="val">@username</div><span class="chev">›</span></div>
    <div class="row" style="top:113px"><i class="ico"></i><div class="lab">Email</div><div class="val">name@brivomail.com</div><span class="chev">›</span></div>
    <div class="row" style="top:135px"><i class="ico"></i><div class="lab">Links</div><div class="val">brivosite.net</div><div class="val">mypage.net</div><div class="val">yourpage.net</div><div style="font-size:4.6px;color:var(--orange)">+Add link</div></div>
    <div class="row" style="top:185px;border:0"><i class="ico"></i><div class="lab">Bio</div><div class="val" style="font-weight:500">A description of this user.</div><span class="chev">›</span></div>
    <div class="ph" role="img" aria-label="Illustration of an elephant reading a book" style="left:84px;top:205px;width:38px;height:36px;background:linear-gradient(#dfe8ef,#a9bccb)"></div>
  </div>
</section>

<!-- BrivoTally -->
<section class="screen stats">
  <div class="status"><span>9:41</span><span class="status-icons"><i style="width:5px;height:3px"></i><i style="width:4px;height:3px"></i><i style="width:7px;height:3px"></i></span></div>
  <div class="app-bar"><span class="menu"><i></i><i></i><i></i></span>BrivoTally<span class="avatar" role="img" aria-label="User profile photo" style="right:7px;top:4px;width:12px;height:12px"></span></div>
  <div class="bar-line"></div>
  <div class="frame"></div>
  <div class="card" style="left:8px;right:8px;top:56px;height:24px;background:transparent"></div>
  <div class="tab" style="left:12px;width:38px;background:var(--cyan)">Ranking</div>
  <div class="tab" style="left:53px;width:54px;background:#e5b3f8">Correct Words</div>
  <div class="tab" style="left:110px;width:30px;background:#e5b3f8">Todo..</div>
  <div class="rank" style="left:12px;width:81px;background:var(--yellow)"><small>Total Ranking</small><strong>1st Place of 100</strong></div>
  <div class="rank" style="left:96px;width:60px;background:var(--green)"><small>Daily Ranking</small><strong>10th Place</strong></div>
  <div class="card stat-card" style="top:124px;height:100px">
    <h3>Learning curve</h3>
    <svg width="124" height="78" viewBox="0 0 124 78" aria-label="Line chart of words learned per day rising over the month" role="img">
      <g font-family="Poppins,sans-serif" font-size="4" fill="#888">
        <text x="0" y="8">100 words per day</text>
        <text x="0" y="21">50 words per day</text>
        <text x="0" y="76">Nov</text><text x="17" y="76">23</text><text x="31" y="76">24</text><text x="44" y="76">25</text><text x="57" y="76">26</text><text x="72" y="76">27</text><text x="86" y="76">28</text><text x="100" y="76">29</text><text x="114" y="76">30</text>
      </g>
      <g stroke="#e6e6e6" stroke-width=".5"><line x1="0" y1="11" x2="122" y2="11"/><line x1="0" y1="24" x2="122" y2="24"/><line x1="0" y1="36" x2="6" y2="36"/><line x1="0" y1="48" x2="6" y2="48"/><line x1="0" y1="60" x2="6" y2="60"/></g>
      <polyline fill="none" stroke="var(--chart)" stroke-width="1" points="0,67 22,65 40,55 46,58 66,45 78,40 88,30 94,36 100,25 106,30 112,20 118,7"/>
      <circle cx="118" cy="7" r="1.6" fill="var(--chart)"/>
    </svg>
  </div>
  <div class="card stat-card list" style="top:231px;height:70px">
    <h3>Recently learned words</h3>
    <div>Ei</div><div>ELA</div><div>Lorem</div><div style="border:0">Lorem</div>
  </div>
</section>

</body>
</html>
```